The design should look similar to the uploaded example to accommodate the information needed for a business card template. I would like to see the colors orange and charcoal grey incorporated along with the logo.The following should be on the back of the card SPECIALIZING IN NEW AND USED TIRES & WHEELS FOR:- Loaders- Skid Steers- Telehandlers- Boom Lifts- Forklifs and moreELIMINATING DOWNTIMEWheel Exchange Program for New & Used Foam Filled and Solid Rubber TiresSPECIALTY SERVICES- Foam Filling Tires- Largest Tire Press in SE- ONSITE Forklift Tire Press- Boom Truck Services - Rubber Tracks

Target Market(s)

New and Existing Customers

Industry/Entity Type

Business

Contact Information for Business Card

NAMEHEAVY DUTY TIRE, LLC8470 Belvedere RoadWest Palm Beach, FL 33411P: 844-HD-TIRESF: 561-431-6469C:E: W: WWW.GRANITERIMSUPPLY-EXAMPLE.COM

Font styles to use
Sans Serif

Colors
f37122
333333

Requirements
Must have
• The logo and the information indicated for the backside of the card
Nice to have
• Keep the orange and charcoal grey colors

```html
<!DOCTYPE html>
<html lang="en">
<head>
<meta charset="utf-8">
<title>Granite Rim Supply, LLC — Business Card</title>
<link href="https://fonts.googleapis.com/css2?family=Open+Sans:wght@400;600;700;800&display=swap" rel="stylesheet">
<style>
  :root {
    --orange: #f37122;
    --charcoal: #333333;
    --slate-dark: #35404a;
    --slate-light: #4d5b67;
    --paper: #ffffff;
    --paper-shade: #ececec;
    --muted: #c9d0d6;
    --backdrop: #e6e3de;
    --rule: #b5b5b5;
  }
  * { box-sizing: border-box; margin: 0; padding: 0; }
  html, body { width: 1200px; height: 950px; overflow: hidden; }
  body {
    background: var(--backdrop);
    font-family: "Open Sans", Arial, sans-serif;
    position: relative;
  }
  .card {
    position: absolute;
    left: 250px;
    width: 700px;
    height: 400px;
    border-radius: 4px;
    box-shadow: 0 10px 30px rgba(0,0,0,.18);
    overflow: hidden;
  }
  .card--back {
    top: 50px;
    background: linear-gradient(160deg, var(--slate-light), var(--slate-dark));
    color: #fff;
    padding: 40px 48px;
  }
  .card--front {
    top: 500px;
    background: linear-gradient(180deg, var(--paper) 60%, var(--paper-shade));
    color: var(--charcoal);
  }
  .brand { display: flex; align-items: center; gap: 14px; }
  .brand__mark {
    width: 64px; height: 64px; border-radius: 50%;
    background: var(--orange); flex: none;
  }
  .brand__name {
    font-weight: 800; font-size: 25px; line-height: 1.1;
    letter-spacing: .5px; text-transform: uppercase;
  }
  .card--back .brand { justify-content: center; margin-bottom: 26px; }
  .card--back .brand__name { color: #fff; }
  .section { margin-bottom: 16px; }
  .section__title {
    font-weight: 700; font-size: 17px; letter-spacing: .4px;
    text-transform: uppercase; margin-bottom: 4px;
  }
  .section__list {
    list-style: none; font-size: 14.5px; color: var(--muted);
    display: flex; flex-wrap: wrap; gap: 2px 0;
  }
  .section__list li + li::before {
    content: "•"; color: var(--orange); margin: 0 8px; font-size: 16px;
  }
  .section__text { font-size: 14.5px; color: var(--muted); }

  .card--front .brand { position: absolute; top: 44px; right: 44px; }
  .card--front .brand__name { color: var(--charcoal); font-size: 24px; }
  .person { position: absolute; left: 48px; top: 170px; }
  .person__name { font-size: 22px; font-weight: 600; text-transform: uppercase; letter-spacing: .5px; }
  .person__title { font-size: 15px; color: var(--orange); text-transform: uppercase; letter-spacing: .5px; margin-bottom: 14px; }
  .contact { list-style: none; font-size: 16px; }
  .contact li { display: flex; align-items: center; gap: 10px; line-height: 27px; }
  .contact svg { width: 17px; height: 17px; fill: var(--charcoal); flex: none; }
  .divider {
    position: absolute; left: 322px; top: 268px; width: 1px; height: 92px;
    background: var(--rule);
  }
  .address {
    position: absolute; left: 350px; top: 272px;
    font-size: 16px; line-height: 27px; font-style: normal;
  }
</style>
</head>
<body>

<section class="card card--back" aria-label="Card back">
  <div class="brand">
    <span class="brand__mark"></span>
    <span class="brand__name">Granite Rim<br>Supply, LLC</span>
  </div>
  <div class="section">
    <h2 class="section__title">Specializing in new and used tires &amp; wheels for</h2>
    <ul class="section__list">
      <li>Loaders</li><li>Skid Steers</li><li>Telehandlers</li><li>Boom Lifts</li><li>Forklifts and more</li>
    </ul>
  </div>
  <div class="section">
    <h2 class="section__title">Eliminating downtime</h2>
    <p class="section__text">Wheel Exchange Program for New &amp; Used Foam Filled and Solid Rubber Tires</p>
  </div>
  <div class="section">
    <h2 class="section__title">Specialty services</h2>
    <ul class="section__list">
      <li>Foam Filling Tires</li><li>Largest Tire Press in SE</li><li>ONSITE Forklift Tire Press</li><li>Boom Truck Services</li><li>Rubber Tracks</li>
    </ul>
  </div>
</section>

<section class="card card--front" aria-label="Card front">
  <div class="brand">
    <span class="brand__mark"></span>
    <span class="brand__name">Granite Rim<br>Supply, LLC</span>
  </div>
  <div class="person">
    <h1 class="person__name">Marcus Hale</h1>
    <p class="person__title">President</p>
    <ul class="contact">
      <li><svg viewBox="0 0 24 24" aria-hidden="true"><path d="M3 8c0-2 2-4 9-4s9 2 9 4v2h-5V8H8v2H3zM6 11h12l2 9H4z"/></svg>844-GR-WHEEL</li>
      <li><svg viewBox="0 0 24 24" aria-hidden="true"><path d="M7 1h10a1 1 0 0 1 1 1v20a1 1 0 0 1-1 1H7a1 1 0 0 1-1-1V2a1 1 0 0 1 1-1zm1 3v14h8V4z"/></svg>836 512 7740</li>
      <li><svg viewBox="0 0 24 24" aria-hidden="true"><path d="M7 2h10v6H7zM3 9h18v10h-4v3H7v-3H3zm6 7v4h6v-4z"/></svg>561-278-9053</li>
      <li><svg viewBox="0 0 24 24" aria-hidden="true"><path d="M2 5h20v2l-10 6L2 7zm0 4l10 6 10-6v10H2z"/></svg>marcus@graniterim-example.com</li>
    </ul>
  </div>
  <div class="divider"></div>
  <address class="address">
    5126 Marston Lane<br>
    Lake Harlow, FL 33490<br>
    www.graniterimsupply-example.com
  </address>
</section>

</body>
</html>
```